QN Banner

I require a 117x 180 flyer based off the attached draft.

-Please make the logo larger, in the centre and stand out more
- Use an appropriate colour palette
- text needs to be larger and capital casing corrected
- add the attached photo (cropped/remove background) as a background to the header of the flyer
- crop out the bra in the photo at the bottom
- Swap second photo (in the section with the gold background) for attached photo kc_9298_

Target Market(s)

health/physio/gym

Industry/Entity Type

Gym

Font styles to use
Sans Serif

Colors

Designer to choose colors to be used in the design.

Requirements
Must have
• Use the logo as the base colour scheme, and see the vantora website - vantoraclinic.com.au for full colour palette.

```html
<!DOCTYPE html>
<html lang="en">
<head>
<meta charset="utf-8">
<title>Le Vantora – Quill North Onsite Physios</title>
<link rel="stylesheet" href="https://fonts.googleapis.com/css2?family=Josefin+Sans:wght@300;400&family=Montserrat:wght@400;500;700;800&display=swap">
<style>
  :root {
    --gold: #b99560;
    --gold-light: #e3aa5f;
    --gold-dark: #98733a;
    --band-gold: #98743a;
    --ink: #111111;
    --charcoal: #1b1b1b;
    --white: #ffffff;
    --text-dark: #222222;
  }
  * { box-sizing: border-box; margin: 0; padding: 0; }
  html, body { width: 831px; height: 1200px; overflow: hidden; background: var(--ink); }
  .flyer { position: relative; width: 831px; height: 1200px; overflow: hidden; background: var(--ink); font-family: "Montserrat", sans-serif; }

  .header-photo {
    position: absolute; left: 0; top: 0; width: 831px; height: 560px;
    background:
      radial-gradient(ellipse 200px 160px at 50% 30%, rgba(120,50,35,.45), transparent 70%),
      linear-gradient(180deg, #2a2a2a 0%, #262626 45%, #161616 85%, var(--ink) 100%);
  }
  .brand { position: absolute; top: 76px; left: 0; width: 100%; text-align: center; }
  .brand-name { font-family: "Josefin Sans", sans-serif; font-weight: 400; font-size: 80px; line-height: 1; color: var(--gold); letter-spacing: 1px; }
  .brand-tagline { font-family: "Josefin Sans", sans-serif; font-weight: 400; font-size: 24px; color: var(--gold); letter-spacing: 5px; margin-top: 10px; }

  .headline { position: absolute; top: 268px; left: 0; width: 100%; text-align: center; font-family: "Josefin Sans", sans-serif; font-weight: 400; }
  .headline-main { font-size: 60px; color: var(--white); line-height: 1; }
  .headline-sub { font-size: 35px; color: var(--white); margin-top: 18px; line-height: 1; }
  .headline-since { font-size: 37px; color: var(--gold); margin-top: 20px; line-height: 1; }

  .services { position: absolute; top: 528px; left: 0; width: 100%; height: 334px; }
  .service { position: absolute; top: 0; width: 202px; height: 334px; }
  .service:nth-child(1) { left: 44px; }
  .service:nth-child(2) { left: 314px; }
  .service:nth-child(3) { left: 586px; }
  .service-card { position: absolute; left: 0; top: 150px; width: 202px; height: 184px; background: var(--white); }
  .service-photo {
    position: absolute; left: -7px; top: 0; width: 216px; height: 216px; border-radius: 50%;
    border: 14px solid var(--gold-light);
    box-shadow: inset 0 0 0 1px var(--gold-dark);
    background-clip: padding-box;
  }
  .service-photo.neck { background: linear-gradient(160deg, #f1f1f1 0%, #c9a998 55%, #b88c78 100%); }
  .service-photo.mobility { background: linear-gradient(100deg, #f2f2f2 0%, #2aa7cf 40%, #1f3f57 70%, #e8e8e8 100%); }
  .service-photo.tape { background: linear-gradient(180deg, #cfcbd4 0%, #b9856a 50%, #a46b52 100%); }
  .service-list { position: absolute; left: 8px; right: 4px; top: 222px; list-style: none; font-size: 13px; line-height: 16px; color: var(--text-dark); }
  .service-list li { position: relative; padding-left: 26px; margin-bottom: 9px; }
  .service-list li.tight { margin-bottom: 3px; }
  .service-list svg { position: absolute; left: 0; top: 0; width: 16px; height: 16px; }

  .divider { position: absolute; top: 862px; left: 0; width: 100%; height: 10px; background: var(--white); }

  .booking { position: absolute; top: 872px; left: 0; width: 100%; height: 164px; background: var(--charcoal); text-align: center; color: var(--white); }
  .booking-title { font-weight: 800; font-size: 42px; color: var(--gold); line-height: 1; margin-top: 26px; }
  .booking-text { font-size: 17.5px; line-height: 24px; margin-top: 6px; }

  .online-bar { position: absolute; top: 1036px; left: 0; width: 100%; height: 42px; background: var(--white); text-align: center; font-weight: 800; font-size: 23px; line-height: 42px; color: var(--ink); }

  .contact { position: absolute; top: 1078px; left: 0; width: 100%; height: 122px; background: var(--ink); }
  .contact-band { position: absolute; inset: 0; }
  .contact-item { position: absolute; top: 42px; display: flex; align-items: center; color: var(--white); font-weight: 800; line-height: 1; }
  .contact-phone { left: 34px; font-size: 36px; }
  .contact-web { left: 352px; font-size: 30px; }
  .contact-item svg { width: 34px; height: 34px; margin-right: 10px; }
</style>
</head>
<body>
<div class="flyer">
  <div class="header-photo" role="img" aria-label="Dim photo of a therapist's hands massaging a client's shoulder"></div>

  <div class="brand">
    <div class="brand-name">LE VANTORA</div>
    <div class="brand-tagline">PHYSIOTHERAPY AND MASSAGE</div>
  </div>

  <div class="headline">
    <div class="headline-main">MEET QUILL NORTH’S</div>
    <div class="headline-sub">VERY OWN ONSITE PHYSIOS!</div>
    <div class="headline-since">PART OF QUILL NORTH SINCE IN 2012</div>
  </div>

  <svg width="0" height="0" style="position:absolute">
    <defs>
      <symbol id="tick" viewBox="0 0 16 16">
        <path d="M13.2 5.2 A6.4 6.4 0 1 1 10.5 2.2" fill="none" stroke="#c48a40" stroke-width="1.6"/>
        <path d="M4.6 7.8 L7.4 10.4 L14 3.4" fill="none" stroke="#c48a40" stroke-width="2" stroke-linecap="round" stroke-linejoin="round"/>
      </symbol>
    </defs>
  </svg>

  <div class="services">
    <div class="service">
      <div class="service-card"></div>
      <div class="service-photo neck" role="img" aria-label="Photo of hands massaging the back of a client's neck"></div>
      <ul class="service-list">
        <li><svg><use href="#tick"/></svg>Repair, Re-align &amp; Rehabilitate your injuries</li>
        <li><svg><use href="#tick"/></svg>Relive pain and stiffness</li>
      </ul>
    </div>
    <div class="service">
      <div class="service-card"></div>
      <div class="service-photo mobility" role="img" aria-label="Photo of a physio assessing a client's posture"></div>
      <ul class="service-list">
        <li><svg><use href="#tick"/></svg>improve mobility and alignment</li>
        <li><svg><use href="#tick"/></svg>Prevent injuries &amp; Achieve your fitness goals</li>
      </ul>
    </div>
    <div class="service">
      <div class="service-card"></div>
      <div class="service-photo tape" role="img" aria-label="Photo of kinesiology tape on a client's upper back"></div>
      <ul class="service-list">
        <li class="tight"><svg><use href="#tick"/></svg>Resolve nagging aches and pains</li>
        <li class="tight"><svg><use href="#tick"/></svg>Posture correction</li>
        <li class="tight"><svg><use href="#tick"/></svg>Biomechanical adjustments for peak performance</li>
      </ul>
    </div>
  </div>

  <div class="divider"></div>

  <section class="booking">
    <h2 class="booking-title">BOOK YOUR</h2>
    <p class="booking-text">free 15min Biomechanical assessment for tips on how to stretch<br>Book your free 15min Biomechanical assessment for tips on how to stretch<br>trigger point and get relief from your pain and stiffness NOW!</p>
  </section>

  <div class="online-bar">VISIT OUR WEBSITE FOR ONLINE BOOKINGS</div>

  <footer class="contact">
    <svg class="contact-band" viewBox="0 0 831 122" preserveAspectRatio="none">
      <polygon points="318,0 831,0 831,122 350,122" fill="#98743a"/>
    </svg>
    <div class="contact-item contact-phone">
      <svg viewBox="0 0 34 34"><circle cx="17" cy="17" r="16" fill="#fff"/><path d="M12 9 q-3 1 -2 8 q2 7 8 8 l2 -3 l-3 -2 l-2 1 q-2 -2 -2 -5 l2 -1 l-1 -4 z" fill="#111"/><path d="M21 13 q2 2 0 5 M23 11 q4 4 0 9" fill="none" stroke="#111" stroke-width="1.4"/></svg>
      0491570156
    </div>
    <div class="contact-item contact-web">
      <svg viewBox="0 0 34 34" fill="none" stroke="#fff" stroke-width="2"><circle cx="17" cy="17" r="14"/><ellipse cx="17" cy="17" rx="6" ry="14"/><line x1="3" y1="17" x2="31" y2="17"/><path d="M6 9 h22 M6 25 h22"/></svg>
      www.vantoraclinic.com
    </div>
  </footer>
</div>
</body>
</html>
```